Web Design Project

This is a wordpress project for a newly formed biologics company based in the US with international clientele. We do manufacturing of biologically based raw materials using a state of the art facility....Our logo must be incorporated....logo colors Navy and Gray. It is fine to use some color in web design. The viewer will primarily be industry folk.

Torvell Biologics, LLC is a contract manufacturing organization which produces biologically-based raw materials derived primarily from human plasma. The company services include extraction and purification of plasma components, especially proteins and enzymes. The business focuses on biotherapeutics, diagnostic and veterinary markets worldwide.

5 pages a bad example of first page can be found in attached files.....
use stock photos of labs and clean rooms.
Updates

Project Deadline Extended
Reason: I need a bit more time tonprovide feedback.

Project Deadline Extended
Reason: needed time to evaluate existing options

Target Market(s)

target market Pharmaceutical companies and research universities

Industry/Entity Type

Veterinary

Requirements
Must have
• our logo...we will provide some graphics...

```html
<!DOCTYPE html>
<html lang="en">
<head>
<meta charset="utf-8">
<title>Torvell Biologics, LLC</title>
<link rel="stylesheet" href="https://fonts.googleapis.com/css2?family=PT+Sans+Narrow:wght@400;700&family=PT+Sans:wght@400;700&display=swap">
<style>
:root{
  --navy:#0d2a55;
  --navy-deep:#03193a;
  --navy-text:#0f2a5c;
  --brand-blue:#114a8a;
  --hero-blue:#0b4a95;
  --hero-light:#3d8fd8;
  --cyan-line:#35c8d8;
  --grey-bar:#adadad;
  --grey-light:#f2f2f2;
  --grey-text:#555b66;
  --footer-link:#c7cdd8;
  --footer-muted:#53627d;
  --white:#ffffff;
}
*{box-sizing:border-box;margin:0;padding:0}
html,body{width:1168px;height:1200px;overflow:hidden}
body{position:relative;background:linear-gradient(#ffffff 0,#ffffff 780px,#b9b9b9 925px);font-family:"PT Sans Narrow",sans-serif;color:var(--navy-text)}
.site-header{position:absolute;left:0;top:0;width:1168px;height:86px;background:linear-gradient(#ffffff,#dcdcdc);border-bottom:2px solid var(--cyan-line)}
.brand{position:absolute;left:54px;top:18px;display:flex;align-items:center;gap:10px}
.brand-dot{width:46px;height:46px;border-radius:50%;background:var(--brand-blue)}
.brand-name{font-family:"PT Sans",sans-serif;font-weight:700;font-size:24px;color:var(--brand-blue)}
.main-nav{position:absolute;right:46px;top:24px;display:flex;gap:10px}
.main-nav a{font-family:"PT Sans",sans-serif;font-weight:700;font-size:23px;color:var(--white);text-decoration:none;padding:4px 14px;text-shadow:0 1px 2px rgba(0,0,0,.55)}
.main-nav a.is-current{background:linear-gradient(#e8e8e8,#a9a9a9);border:1px solid #7d8ea4;border-radius:6px}
.hero{position:absolute;left:30px;top:88px;width:1098px;height:246px;background:linear-gradient(160deg,#0a3a7c 0%,#1261b3 45%,#0a3a7c 100%);overflow:hidden;border-bottom:2px solid #0a2040}
.hero-band{position:absolute;left:0;bottom:0;width:100%;height:40px;background:linear-gradient(#1a6fc4,#0c3f84)}
.slide{position:absolute;border:2px solid rgba(255,255,255,.8)}
.slide-left{left:240px;top:32px;width:154px;height:192px;background:linear-gradient(#eef3f8,#9fb7d0)}
.slide-right{left:728px;top:32px;width:220px;height:192px;background:linear-gradient(#f0f5fb,#a3bcd7)}
.slide-main{left:394px;top:12px;width:334px;height:224px;background:linear-gradient(#f4f7fa,#b5c8dc);box-shadow:0 0 14px rgba(0,0,0,.35)}
.slide-dots{position:absolute;left:508px;top:214px;display:flex;gap:7px}
.slide-dots span{width:24px;height:24px;border-radius:50%;background:#2f7fd0;color:var(--white);font-family:"PT Sans",sans-serif;font-size:15px;text-align:center;line-height:24px}
.slide-dots span.is-active{background:#041c3d}
.welcome{position:absolute;left:46px;top:354px;width:1050px;height:239px;background:linear-gradient(90deg,#f7f7f7,#ffffff 50%,#ececec)}
.welcome-bar{height:48px;background:var(--grey-bar);border-bottom:2px solid var(--cyan-line);position:relative}
.welcome-bar h1{position:absolute;left:14px;top:3px;font-weight:700;font-size:34px;color:var(--white);text-shadow:0 1px 3px rgba(0,0,0,.45)}
.search{position:absolute;right:10px;top:6px;width:208px;height:30px;background:var(--white);border:1px solid #bbb;border-radius:3px;font-family:"PT Sans",sans-serif;font-size:12px;color:#888;padding:8px 10px}
.search i{position:absolute;right:0;top:0;width:26px;height:28px;background:#d6d6d6}
.welcome-copy{position:absolute;left:26px;top:84px;width:996px;font-size:20.5px;line-height:29px}
.welcome-rule{position:absolute;left:26px;right:30px;top:218px;border-top:2px dashed #c4c4c4}
.more{position:absolute;right:30px;top:204px;font-family:"PT Sans",sans-serif;font-size:20px;color:#999}
.lab-photo{position:absolute;left:52px;top:613px;width:406px;height:282px;border:1px solid #2a5185;background:linear-gradient(#f5f7f9,#c9d6e2 70%,#8aa2ba)}
.expertise{position:absolute;left:485px;top:613px;width:611px;height:227px;background:radial-gradient(ellipse at 40% 50%,#ffffff,#e6e6e6);padding:20px 24px;font-size:20.5px;line-height:29px}
.expertise p+p{margin-top:29px}
.contact-note{position:absolute;left:509px;top:855px;font-size:20.5px}
.site-footer{position:absolute;left:0;top:925px;width:1168px;height:275px;background:linear-gradient(var(--navy-deep),#02142e)}
.footer-col{position:absolute;top:60px;list-style:none;font-family:"PT Sans",sans-serif;font-size:20px;line-height:26.4px}
.footer-main{left:74px;color:var(--footer-link)}
.footer-quick{color:var(--footer-muted)}
.divider{position:absolute;top:30px;width:1px;height:180px;background:#1b3761}
.follow{position:absolute;left:956px;top:50px;font-family:"PT Sans",sans-serif;font-size:20px;color:var(--footer-muted)}
.social{position:absolute;left:960px;top:84px;display:flex;gap:10px}
.social span{width:28px;height:28px;border-radius:3px;background:#4f7fbf}
.footer-search{position:absolute;left:954px;top:137px;width:157px;height:27px;background:linear-gradient(#1d4f97,#0f3470);border:1px solid #3c66a4;font-family:"PT Sans",sans-serif;font-size:14px;color:var(--white);padding:4px 10px}
.footer-search i{position:absolute;right:0;top:0;width:19px;height:25px;background:#8094b3}
.copyright{position:absolute;left:0;top:232px;width:1168px;text-align:center;font-family:"PT Sans",sans-serif;font-size:13px;color:var(--footer-muted)}
</style>
</head>
<body>
<header class="site-header">
  <div class="brand"><span class="brand-dot"></span><span class="brand-name">Torvell Biologics</span></div>
  <nav class="main-nav">
    <a class="is-current" href="#">Home</a><a href="#">Facilities</a><a href="#">Team</a><a href="#">Announcements</a><a href="#">Contact</a>
  </nav>
</header>

<section class="hero">
  <div class="hero-band"></div>
  <div class="slide slide-left" role="img" aria-label="Clean room with lab benches"></div>
  <div class="slide slide-right" role="img" aria-label="Clean room corridor with glass doors"></div>
  <div class="slide slide-main" role="img" aria-label="Clean room with microscope and lab equipment"></div>
  <div class="slide-dots"><span>1</span><span>2</span><span class="is-active">3</span><span>4</span></div>
</section>

<section class="welcome">
  <div class="welcome-bar">
    <h1>Welcome</h1>
    <div class="search">Search<i></i></div>
  </div>
  <p class="welcome-copy">Torvell Biologics (TBL) is a Contract Manufacturing Organization (CMO) located in Sarasota, Florida.<br>TBL is currently in the process of commissioning a state-of-the-art biological manufacturing facility using the Vexlon- Single Use Disposable Plastic Bags which reduces risks of cross-contamination between batches. TBL has a fully equipped Quality Control laboratory and Process Development Laboratory.</p>
  <div class="welcome-rule"></div>
  <span class="more">&gt;&gt;</span>
</section>

<div class="lab-photo" role="img" aria-label="Bright laboratory with workbenches and a researcher at a station"></div>

<section class="expertise">
  <p>TBL's core expertise is in plasma derived components for the human, veterinary and diagnostic market. The nature of its facility will allow to evaluate other biological based raw material for extraction and purification.</p>
  <p>Our facility is ideal for GMP components for pre-clinical, clinical and commercial launch production.</p>
</section>
<p class="contact-note">For additional information, please contact us with your project.</p>

<footer class="site-footer">
  <ul class="footer-col footer-main"><li>Home</li><li>Facilities</li><li>Team</li><li>Links</li><li>Contact</li></ul>
  <span class="divider" style="left:216px"></span>
  <ul class="footer-col footer-quick" style="left:260px"><li>Some Quick Links</li><li>Some Quick Links</li><li>Some Quick Links</li><li>Some Quick Links</li><li>Some Quick Links</li></ul>
  <span class="divider" style="left:463px"></span>
  <ul class="footer-col footer-quick" style="left:490px"><li>Some Quick Links</li><li>Some Quick Links</li><li>Some Quick Links</li><li>Some Quick Links</li><li>Some Quick Links</li></ul>
  <span class="divider" style="left:695px"></span>
  <ul class="footer-col footer-quick" style="left:728px"><li>Some Quick Links</li><li>Some Quick Links</li><li>Some Quick Links</li><li>Some Quick Links</li><li>Some Quick Links</li></ul>
  <span class="divider" style="left:924px"></span>
  <p class="follow">Follow us</p>
  <div class="social"><span role="img" aria-label="Social profile link"></span><span role="img" aria-label="Social profile link"></span></div>
  <div class="footer-search">Search<i></i></div>
  <p class="copyright">Copyright ©201 Torvell Biologics</p>
</footer>
</body>
</html>
```